New Business Card Design Project

We require a business card design for Vexalund, a newly established Indian company.
Our focus is on the development, manufacturing, and export of a diverse array of pharmaceutical products on a global scale. The card should convey a professional appearance, as our primary markets are in Africa, China, and Southeast Asian nations.
We envision a two-sided business card, with the reverse side dedicated to a logo set against a solid color or an elegantly designed pattern. The corners should be rounded. We would appreciate seeing both horizontal and vertical design options. We trust the designer to utilize their expertise in creating this design.

The content for the business card is included in the attached Word file.

Target Market(s)

Our primary markets are in Africa, China, and Southeast Asian, Latin America, Maldives, Sri Lanka

Industry/Entity Type

Pharmaceutical Manufacturing and Export

Contact Information for Business Card

Colors

Designer to choose colors to be used in the design.

Requirements
Must have
• The reverse side of the business card features solely the logo along with the tagline, "Care in Every Dose."
Should not have
• The logo should not exceed two instances, encompassing both the front and back sides of the card.

```html
<!DOCTYPE html>
<html lang="en">
<head>
<meta charset="utf-8">
<title>Vexalund Business Card</title>
<link href="https://fonts.googleapis.com/css2?family=Montserrat:wght@400;700&family=Open+Sans:wght@400;600&display=swap" rel="stylesheet">
<style>
  :root {
    --backdrop: #232323;
    --card: #202024;
    --blue: #2ea5df;
    --coral: #f0604d;
    --white: #f2f2f2;
  }
  * { margin: 0; padding: 0; box-sizing: border-box; }
  html, body { width: 1200px; height: 711px; overflow: hidden; background: var(--backdrop); }
  .stage { position: relative; width: 1200px; height: 711px; }
  .card {
    position: absolute; top: 200px; width: 540px; height: 310px;
    background: var(--card); border-radius: 26px; overflow: hidden;
    box-shadow: 0 8px 24px rgba(0,0,0,.55);
  }
  .card--back { left: 40px; }
  .card--front { left: 620px; }
  .accent-bar { position: absolute; width: 12px; background: var(--coral); }
  .accent-bar--left { left: 22px; top: 150px; height: 120px; }
  .accent-bar--right { right: 22px; top: 40px; height: 120px; }

  .brand { font-family: 'Montserrat', sans-serif; font-weight: 700; color: var(--blue); display: flex; align-items: center; gap: 12px; white-space: nowrap; }
  .brand-dot { width: 16px; height: 16px; border-radius: 50%; background: var(--coral); }
  .card--back .brand { position: absolute; left: 0; right: 0; top: 115px; justify-content: center; font-size: 54px; letter-spacing: -1px; }
  .tagline { position: absolute; left: 0; right: 0; top: 192px; text-align: center; font-family: 'Montserrat', sans-serif; font-size: 13px; color: var(--blue); letter-spacing: .5px; }

  .card--front .brand { position: absolute; left: 48px; top: 128px; font-size: 38px; letter-spacing: -1px; }
  .card--front .brand-dot { width: 12px; height: 12px; }
  .divider { position: absolute; left: 272px; top: 62px; width: 1px; height: 150px; background: var(--blue); }
  .person { position: absolute; left: 296px; top: 68px; font-family: 'Montserrat', sans-serif; white-space: nowrap; }
  .person-name { font-size: 21px; color: var(--coral); font-weight: 400; }
  .person-name strong { color: var(--blue); font-weight: 700; }
  .person-role { font-family: 'Open Sans', sans-serif; font-size: 12px; color: var(--white); margin-top: 2px; }
  .contact-list { position: absolute; left: 296px; top: 138px; list-style: none; font-family: 'Open Sans', sans-serif; font-size: 12.5px; color: var(--white); white-space: nowrap; }
  .contact-list li { display: flex; align-items: center; gap: 8px; height: 22px; }
  .contact-list svg { width: 14px; height: 14px; flex: none; }
  .address { position: absolute; left: 0; right: 0; bottom: 34px; text-align: center; font-family: 'Open Sans', sans-serif; font-size: 13px; color: var(--blue); white-space: nowrap; }
</style>
</head>
<body>
<main class="stage">
  <section class="card card--back" aria-label="Card back">
    <div class="accent-bar accent-bar--left"></div>
    <div class="accent-bar accent-bar--right"></div>
    <div class="brand"><span class="brand-dot"></span>Vexalund</div>
    <p class="tagline">Care in Every Dose.</p>
  </section>

  <section class="card card--front" aria-label="Card front">
    <div class="accent-bar accent-bar--left"></div>
    <div class="accent-bar accent-bar--right"></div>
    <div class="brand"><span class="brand-dot"></span>Vexalund</div>
    <div class="divider"></div>
    <div class="person">
      <p class="person-name"><strong>Arjun</strong> K. Malvade</p>
      <p class="person-role">CEO</p>
    </div>
    <ul class="contact-list">
      <li>
        <svg viewBox="0 0 14 14"><rect x="3" y="1" width="8" height="12" rx="1.5" fill="none" stroke="#f0604d" stroke-width="1.4"/></svg>
        +919 555018273
      </li>
      <li>
        <svg viewBox="0 0 14 14"><circle cx="7" cy="7" r="6" fill="#2ea5df"/><path d="M1 7h12M7 1c-2.5 3-2.5 9 0 12M7 1c2.5 3 2.5 9 0 12" stroke="#202024" stroke-width="1" fill="none"/></svg>
        www.vexalund.com
      </li>
      <li>
        <svg viewBox="0 0 14 14"><rect x="1" y="3" width="12" height="9" rx="1" fill="#f0604d"/><path d="M1.5 3.5 7 8l5.5-4.5" stroke="#202024" stroke-width="1.2" fill="none"/></svg>
        amalvade@vexalund.com
      </li>
    </ul>
    <p class="address">12, Sarita Nagar, Devgiri, 440011, India</p>
  </section>
</main>
</body>
</html>
```